Allied Health team of Physiotherapists & Occupational Therapists seek a business card design

We have our new logo, we now need our new business cards and stationary. Tidewell: Oedema & Family Clinic is seeking a generic card design to represent our whole team and individual cards for each therapist that incorporates our new logo to communicate our holistic approach that is calming, nuturing, supportive and welcoming.
Our Physiotherapists and Occupational Therapists assess, treat and provide education for people who are at risk of or who have lymphoedema. This is often as a result of treatment for cancer. We provide pre-operative and post-operative management and cancer rehabilitation in our Pilates studio. Our team also consists of Physiotherapists who have a strong interest in pelvic floor and continence management for both men and women.

Target Market(s)

Mainly women health conscious

Industry/Entity Type

Allied Health: Physiotherapy / Occupational Therapy

Contact Information for Business Card

Address: 14 Gallivant Ave Frankston 3199 Phone: 84316570 fax: 8431 6578 Email: info@tidewellcareservices.com.au Website: tidewellcareservices.com.au Facebook address: facebook.com/TidewellOedemaAndFamilyCareClinic. Room to write appointments. Individual cards need to have name, office email and individual email and professional details

Requirements
Must have
• Logo as per uploaded documents

```html
<!DOCTYPE html>
<html lang="en">
<head>
<meta charset="utf-8">
<title>Tidewell Business Card</title>
<link rel="stylesheet" href="https://fonts.googleapis.com/css2?family=Crimson+Pro:wght@700&family=Open+Sans:wght@400;600&display=swap">
<style>
  :root {
    --peach: #f8b185;
    --sage: #c4cec3;
    --ink: #333132;
    --paper: #ffffff;
    --backdrop: #2a2728;
  }
  * { margin: 0; padding: 0; box-sizing: border-box; }
  html, body { width: 1133px; height: 1200px; overflow: hidden; }
  body {
    background: var(--backdrop);
    font-family: "Open Sans", Arial, sans-serif;
    position: relative;
  }
  .card {
    position: absolute;
    left: 173px;
    width: 822px;
    height: 468px;
    overflow: hidden;
  }
  .card--front { top: 102px; background: var(--paper); }
  .card--back { top: 628px; background: var(--peach); }

  .brand-name {
    position: absolute;
    left: 0; right: 0;
    text-align: center;
    font-family: "Open Sans", Arial, sans-serif;
    font-weight: 600;
  }
  .card--front .brand-name {
    top: 88px;
    font-size: 17px;
    color: var(--peach);
    letter-spacing: 0.5px;
  }
  .card--back .brand-name {
    top: 222px;
    font-size: 28px;
    color: var(--paper);
    letter-spacing: 0.8px;
  }

  .person {
    position: absolute;
    right: 452px;
    top: 228px;
    white-space: nowrap;
  }
  .person__name {
    font-family: "Crimson Pro", Georgia, serif;
    font-weight: 700;
    font-size: 22px;
    color: var(--peach);
    line-height: 1;
    letter-spacing: 0.3px;
  }
  .person__role {
    font-size: 11px;
    color: var(--ink);
    margin-top: 1px;
    margin-left: 3px;
  }

  .divider {
    position: absolute;
    left: 393px;
    top: 227px;
    width: 1px;
    height: 150px;
    background: var(--ink);
  }

  .address {
    position: absolute;
    left: 410px;
    top: 227px;
    font-size: 14px;
    line-height: 21px;
    color: var(--ink);
    white-space: nowrap;
  }

  .contacts {
    position: absolute;
    left: 410px;
    top: 301px;
    list-style: none;
    font-size: 14px;
    color: var(--ink);
    white-space: nowrap;
  }
  .contacts li {
    display: flex;
    align-items: center;
    height: 26px;
  }
  .contacts svg {
    width: 19px;
    height: 19px;
    margin-right: 9px;
    flex: none;
  }

  .waves {
    position: absolute;
    left: 0;
    bottom: 0;
    width: 822px;
    height: 80px;
  }
</style>
</head>
<body>

<section class="card card--front">
  <div class="brand-name">Tidewell: Oedema &amp; Family Clinic</div>

  <div class="person">
    <div class="person__name">MARA ELLSWORTH</div>
    <div class="person__role">CEO/Managing Director</div>
  </div>

  <div class="divider"></div>

  <div class="address">
    14 Gallivant Avenue<br>
    Suite 2, Frankston VIC 3199
  </div>

  <ul class="contacts">
    <li>
      <svg viewBox="0 0 20 20" fill="none" stroke="var(--peach)" stroke-width="1.6" stroke-linecap="round" stroke-linejoin="round">
        <path d="M4 3l3 0 1.5 4-2 1.3a9 9 0 0 0 5.2 5.2l1.3-2 4 1.5v3a1.5 1.5 0 0 1-1.6 1.5A14 14 0 0 1 2.5 4.6 1.5 1.5 0 0 1 4 3z"/>
        <path d="M12 2.5a6 6 0 0 1 5.5 5.5"/>
        <path d="M12 5.5a3 3 0 0 1 2.5 2.5"/>
      </svg>
      8431-6570
    </li>
    <li>
      <svg viewBox="0 0 20 20" fill="var(--peach)">
        <path d="M2 5h16v10H2z" />
        <path d="M2 5l8 6 8-6" fill="none" stroke="#fff" stroke-width="1.3"/>
      </svg>
      mara@tidewellcareservices.com.au
    </li>
    <li>
      <svg viewBox="0 0 20 20" fill="none" stroke="var(--peach)" stroke-width="1.3">
        <circle cx="10" cy="10" r="8"/>
        <ellipse cx="10" cy="10" rx="3.5" ry="8"/>
        <path d="M2 10h16M3.5 6h13M3.5 14h13"/>
      </svg>
      www.tidewellcareservices.com.au
    </li>
  </ul>

  <svg class="waves" viewBox="0 0 822 80" preserveAspectRatio="none" aria-hidden="true">
    <path d="M0 0 C 90 30, 240 36, 400 26 C 560 8, 700 -2, 822 20 L 822 44 C 700 20, 560 24, 420 30 C 280 38, 110 50, 0 24 Z" fill="var(--sage)"/>
    <path d="M0 30 C 110 56, 280 48, 420 36 C 560 26, 700 26, 822 50 L 822 80 L 0 80 Z" fill="var(--peach)"/>
  </svg>
</section>

<section class="card card--back">
  <div class="brand-name">Tidewell: Oedema &amp; Family Clinic</div>
</section>

</body>
</html>
```